Brochure and Business Card design

I am looking for a high end, elegant A4, 4 page brochure booklet to convey our products to clientele that will be visiting a luxury display showroom.

Harrowgate Locks and Grilles is a Australian security provider, and we supply high end products from reputable brands.
The brochure will be directed to clients building a new home with a partnered building company and will be accompanied with display boards of our products.

I am providing files of a document we have put together with the relevant information and some images to help along the way, we are not bound by the layout or style it has been drawn up and we wish to give you complete creative freedom putting the peaces together. I have also provided the files for our logo in two different colours, and a picture of a brochure we love the look of.

If you have any suggestions, we can likely come up with further images etc if it will help or even if you feel some should be removed, we are open to that also

Target Market(s)

Young familys, people building new luxury homes, proffesionals, home owners

Industry/Entity Type

Business

Font styles to use
Serif
Sans Serif

Requirements
Must have
• All 8 pages
Should not have
• Not really a fan of reds and similar.

```html
<!DOCTYPE html>
<html lang="en">
<head>
<meta charset="utf-8">
<title>Harrowgate Locks and Grilles – Brochure Spreads</title>
<link href="https://fonts.googleapis.com/css2?family=Didact+Gothic&family=Open+Sans:wght@400;600;700&display=swap" rel="stylesheet">
<style>
  :root{
    --bg:#d2d2d2;
    --paper:#ffffff;
    --blue:#2a86c7;
    --blue-dark:#1f6fab;
    --green:#8cc540;
    --ink:#555b60;
    --ink-soft:#8b9095;
    --photo-cool:#b9c2c9;
    --photo-warm:#d9c7b3;
    --photo-grey:#9ea3a7;
  }
  *{box-sizing:border-box;margin:0;padding:0}
  html,body{width:1200px;height:754px;overflow:hidden}
  body{background:var(--bg);font-family:"Open Sans",sans-serif;color:var(--ink);position:relative}
  .spread{position:absolute;width:540px;height:260px;display:flex;box-shadow:0 6px 18px rgba(0,0,0,.22)}
  .spread--covers{left:30px;top:58px}
  .spread--alarm{left:630px;top:58px}
  .spread--mesh{left:30px;top:436px}
  .spread--vacuum{left:630px;top:436px}
  .page{position:relative;width:270px;height:260px;background:var(--paper);overflow:hidden}
  .page--left{border-right:1px solid #e6e6e6}
  .abs{position:absolute}
  .body-copy{font-size:5.6px;line-height:1.5;color:var(--ink-soft)}
  .heading{font-family:"Didact Gothic",sans-serif;font-weight:400}
  .label{font-size:6px;font-weight:700;color:var(--green);text-transform:uppercase;letter-spacing:.3px}
  .sub{font-size:6.2px;font-weight:700;color:var(--green)}
  .photo{background:linear-gradient(135deg,var(--photo-cool),var(--photo-grey))}
  .photo--warm{background:linear-gradient(135deg,var(--photo-warm),#c9b29a)}
  .product{background:linear-gradient(160deg,#eceeef,#b8bcbf);border-radius:2px}

  .brand{display:flex;align-items:center;gap:5px}
  .brand__dot{width:10px;height:10px;border-radius:50%;background:var(--green)}
  .brand__name{font-family:"Didact Gothic",sans-serif;color:var(--ink);letter-spacing:.5px}
  .brand__tag{font-size:4.6px;letter-spacing:1.2px;color:var(--green);margin-left:15px}

  .back-cover__intro{left:30px;right:30px;top:90px;text-align:center}
  .back-cover__intro p+p{margin-top:6px}
  .contact-band{left:0;right:0;bottom:0;height:92px;background:linear-gradient(100deg,var(--blue-dark),var(--blue) 60%,#5aa7da);color:#fff;text-align:center;padding-top:20px}
  .contact-band__title{font-size:6.4px;font-weight:700}
  .contact-band__line{font-size:5px;margin-top:5px;opacity:.9}
  .contact-band__web{font-size:7.4px;font-weight:700;margin-top:6px}
  .contact-band__note{font-size:4.2px;margin-top:12px;opacity:.75}
  .cover-grid{left:0;top:0;width:270px;height:132px;display:grid;grid-template-columns:repeat(4,1fr);grid-template-rows:1fr 1fr}
  .tile--blue{background:var(--blue)}
  .tile--green{background:var(--green)}
  .front-cover__brand{left:95px;top:158px}
  .front-cover__web{left:0;right:0;top:196px;text-align:center;font-size:6px;color:var(--ink-soft);letter-spacing:.4px}

  .page-title{font-size:15px;color:var(--blue)}
  .product-row{display:flex;flex-wrap:wrap;gap:8px 10px}
  .product-item{display:flex;align-items:center;gap:4px;width:70px}
  .product-item .product{width:18px;height:18px;flex:none}
  .product-item span{font-size:4.8px;color:var(--ink-soft)}
  .intercom-item{display:flex;gap:8px;margin-bottom:10px}
  .intercom-item .product{width:28px;height:22px;flex:none}

  .feature{display:flex;gap:10px;margin-bottom:14px}
  .feature .product{width:34px;height:26px;flex:none}
  .feature h4{font-size:6.4px;font-weight:700;color:var(--green);margin-bottom:2px}
</style>
</head>
<body>

<section class="spread spread--covers">
  <div class="page page--left">
    <div class="abs brand" style="left:94px;top:58px">
      <span class="brand__dot"></span><span class="brand__name" style="font-size:13px">HARROWGATE</span>
    </div>
    <div class="abs back-cover__intro body-copy">
      <p>Harrowgate Locks and Grilles supplies premium security products from trusted brands for new luxury homes.</p>
      <p>Visit our showroom to explore display boards with our team.</p>
    </div>
    <div class="abs contact-band">
      <p class="contact-band__title">For all inquiries</p>
      <p class="contact-band__line">Email: hello@harrowgatelocks.com.au &nbsp;|&nbsp; Phone: 03 9000 4127</p>
      <p class="contact-band__web">www.harrowgatelocks.com.au</p>
      <p class="contact-band__note">Product brands shown remain property of their owners.</p>
    </div>
  </div>
  <div class="page">
    <div class="abs cover-grid">
      <div class="photo" role="img" aria-label="Modern two-storey home facade"></div>
      <div class="tile--green"></div>
      <div class="photo--warm" role="img" aria-label="New home with garage and front gate"></div>
      <div class="tile--green"></div>
      <div class="tile--blue"></div>
      <div class="photo" role="img" aria-label="Contemporary timber and render home"></div>
      <div class="tile--blue"></div>
      <div class="photo" role="img" aria-label="Wall-mounted intercom beside a door"></div>
    </div>
    <div class="abs front-cover__brand">
      <div class="brand"><span class="brand__dot"></span><span class="brand__name" style="font-size:14px">HARROWGATE</span></div>
      <div class="brand__tag">LOCKS AND GRILLES</div>
    </div>
    <p class="abs front-cover__web">www.harrowgatelocks.com.au</p>
  </div>
</section>

<section class="spread spread--alarm">
  <div class="page page--left">
    <h2 class="abs heading page-title" style="left:18px;top:16px">Alarm Systems</h2>
    <p class="abs body-copy" style="left:18px;top:40px;width:112px">Protect your new home with monitored alarm systems, motion sensors and smart control panels installed by our licensed team.</p>
    <div class="abs photo" style="left:140px;top:16px;width:130px;height:62px" role="img" aria-label="Alarm keypad mounted on a hallway wall"></div>
    <p class="abs label" style="left:140px;top:84px">Home kits</p>
    <svg class="abs" style="left:0;top:88px" width="270" height="40" viewBox="0 0 270 40" aria-hidden="true">
      <polygon points="120,4 270,0 270,22 120,30" fill="var(--blue)"/>
    </svg>
    <p class="abs" style="left:135px;top:100px;font-size:5.4px;color:#fff;font-weight:600">Smart alarm control from your phone</p>
    <p class="abs label" style="left:18px;top:124px">Popular upgrades</p>
    <div class="abs product-row" style="left:18px;top:140px;width:240px">
      <div class="product-item"><div class="product" role="img" aria-label="Motion sensor"></div><span>PIR sensor</span></div>
      <div class="product-item"><div class="product" role="img" aria-label="Smoke detector"></div><span>Smoke detector</span></div>
      <div class="product-item"><div class="product" role="img" aria-label="Keypad remote"></div><span>Keypad remote</span></div>
      <div class="product-item"><div class="product" role="img" aria-label="Siren strobe"></div><span>Siren strobe</span></div>
      <div class="product-item"><div class="product" role="img" aria-label="Glass break sensor"></div><span>Glass break</span></div>
      <div class="product-item"><div class="product" role="img" aria-label="Door reed switch"></div><span>Door reed</span></div>
    </div>
  </div>
  <div class="page">
    <div class="abs photo" style="left:150px;top:0;width:120px;height:58px;opacity:.6" role="img" aria-label="Bright entry hall with intercom panel"></div>
    <h2 class="abs heading page-title" style="left:16px;top:16px">Intercom</h2>
    <p class="abs body-copy" style="left:16px;top:38px;width:130px">See and speak with visitors from any room using modern video intercom systems.</p>
    <div class="abs" style="left:16px;top:72px;width:150px">
      <div class="intercom-item"><div class="product" role="img" aria-label="Seven inch video intercom"></div><div><p class="sub">7" Colour Video Intercom</p><p class="body-copy">Hands free monitor with clear night vision camera.</p></div></div>
      <div class="intercom-item"><div class="product" role="img" aria-label="Compact video intercom"></div><div><p class="sub">4.3" Colour Video Intercom</p><p class="body-copy">Compact screen with wide angle weatherproof door camera.</p></div></div>
      <div class="intercom-item"><div class="product" role="img" aria-label="Audio intercom handset"></div><div><p class="sub">Audio Only Intercom</p><p class="body-copy">Simple handset with crisp sound and door release.</p></div></div>
    </div>
    <p class="abs label" style="left:180px;top:66px">Popular upgrades</p>
    <div class="abs" style="left:180px;top:80px;width:80px">
      <div class="intercom-item"><div class="product" style="width:18px;height:22px" role="img" aria-label="Indoor monitor"></div><p class="body-copy">Extra indoor monitor</p></div>
      <div class="intercom-item"><div class="product" style="width:18px;height:22px" role="img" aria-label="Door station"></div><p class="body-copy">Slim door station</p></div>
      <div class="intercom-item"><div class="product" style="width:18px;height:22px" role="img" aria-label="Electric strike"></div><p class="body-copy">Electric strike lock</p></div>
    </div>
  </div>
</section>

<section class="spread spread--mesh">
  <div class="page page--left">
    <div class="abs photo" style="left:0;top:0;width:270px;height:130px;background:linear-gradient(135deg,#eef0f1,#5d6368)" role="img" aria-label="Close-up of security screen door and mesh"></div>
    <svg class="abs" style="left:0;top:60px" width="270" height="200" viewBox="0 0 270 200" aria-hidden="true">
      <defs>
        <linearGradient id="meshBand" x1="0" y1="0" x2="1" y2="0">
          <stop offset="0" stop-color="var(--blue-dark)"/><stop offset=".7" stop-color="var(--blue)"/><stop offset="1" stop-color="#6fb3e0"/>
        </linearGradient>
      </defs>
      <path d="M0 30 Q140 0 270 20 L270 200 L0 200 Z" fill="url(#meshBand)"/>
    </svg>
    <h2 class="abs heading" style="left:60px;top:112px;font-size:15px;color:#fff">Why Stalwart Mesh?</h2>
    <p class="abs body-copy" style="left:60px;top:136px;width:150px;color:rgba(255,255,255,.85)">Stalwart Mesh screens combine a stainless steel weave with a strong frame for security, airflow and a clear outlook.</p>
  </div>
  <div class="page">
    <div class="abs" style="left:18px;top:26px;width:240px">
      <div class="feature"><div class="product" role="img" aria-label="Mesh strength detail"></div><div><h4>Strength</h4><p class="body-copy">Tested against impact and knife attack to keep every opening secure year round.</p></div></div>
      <div class="feature"><div class="product" role="img" aria-label="Mesh safety detail"></div><div><h4>Safety</h4><p class="body-copy">Lets fresh air in while keeping children, pets and intruders safely on the right side.</p></div></div>
      <div class="feature"><div class="product" role="img" aria-label="Mesh visibility detail"></div><div><h4>Visual Clarity</h4><p class="body-copy">Fine mesh gives a clear view outside with little loss of natural light.</p></div></div>
      <div class="feature"><div class="product" role="img" aria-label="Mesh frame detail"></div><div><h4>Australian Design</h4><p class="body-copy">Made to suit Australian homes and built to handle our harsh coastal conditions.</p></div></div>
    </div>
  </div>
</section>

<section class="spread spread--vacuum">
  <div class="page page--left">
    <div class="abs photo--warm" style="left:0;top:0;width:270px;height:150px;background:linear-gradient(135deg,#e7e3de,#d8b9a2)" role="img" aria-label="Happy family relaxing at home"></div>
    <svg class="abs" style="left:0;top:0" width="270" height="260" viewBox="0 0 270 260" aria-hidden="true">
      <path d="M0 78 C100 58 200 58 270 92 L270 215 C190 168 100 152 0 142 Z" fill="var(--green)"/>
    </svg>
    <div class="abs product" style="left:14px;top:94px;width:80px;height:36px;background:linear-gradient(160deg,#6c7175,#2f3336)" role="img" aria-label="Vacuum hose and cleaning tools"></div>
    <h2 class="abs heading" style="left:110px;top:96px;font-size:14px;color:#fff">Ducted Vacuum</h2>
    <p class="abs body-copy" style="left:110px;top:118px;width:110px;color:rgba(255,255,255,.92)">A ducted vacuum removes fine dust from living areas and suits busy young families.</p>
  </div>
  <div class="page">
    <div class="abs product" style="left:16px;top:50px;width:62px;height:110px;border-radius:10px/6px;background:linear-gradient(90deg,#6e7478,#a5aaae 45%,#585d61)" role="img" aria-label="Ducted vacuum power unit"></div>
    <div class="abs" style="left:92px;top:40px;width:80px">
      <p class="sub">Powerful Whole Home Suction</p>
      <p class="body-copy" style="margin-bottom:10px">Strong motors reach every room through hidden pipes, so you carry only a light hose.</p>
      <p class="sub">Quiet, Simple Cleaning</p>
      <p class="body-copy">The power unit sits in the garage, keeping noise away from living spaces.</p>
    </div>
    <div class="abs" style="left:182px;top:60px;width:74px">
      <p class="sub">Great Value for Your Home</p>
      <p class="body-copy" style="margin-bottom:10px">Adds lasting value to a new build and is easy to plan in early.</p>
      <p class="sub">Low Maintenance</p>
      <p class="body-copy">Large bins need emptying only a few times a year with no bags required.</p>
    </div>
  </div>
</section>

</body>
</html>
```